Bry7Legal Letterhead

Need a new letterhead for my law firm.
IDENTIFYING INFORMATION BELOW:
Anselmo R Quintara III
Attorney at Law
Address: 2847 Larkspur Blvd, Ste 300, Dallas, TX 75204
Phone: 877-482-6017
Fax: 469-738-1452
Email: bry@bry7legal.example
Website: www.bry7legal.example

Colors
0054AA
0677BA
7BADD7
CADEEF
E8F1F8

Requirements
Must have
• Logo needs to be on the letterhead, along with identifying information which is included in the project description.

```html
<!DOCTYPE html>
<html lang="en">
<head>
<meta charset="utf-8">
<title>Bry7Legal Letterhead</title>
<link href="https://fonts.googleapis.com/css2?family=Montserrat:wght@300;400;600;800&display=swap" rel="stylesheet">
<style>
  :root {
    --backdrop: #e6e7e8;
    --paper: #ffffff;
    --ink: #161616;
    --brand-blue: #0677ba;
    --brand-deep: #0054aa;
    --text-light: #ffffff;
    --tagline: #2a2a2a;
  }
  * { margin: 0; padding: 0; box-sizing: border-box; }
  html, body {
    width: 1200px; height: 874px; overflow: hidden;
    background: var(--backdrop);
    font-family: "Montserrat", Arial, sans-serif;
  }
  .letterhead {
    position: absolute;
    left: 291px; top: 37px;
    width: 618px; height: 800px;
    background: var(--paper);
    box-shadow: 0 10px 30px rgba(0,0,0,0.18);
    overflow: hidden;
  }
  .brand {
    position: absolute; left: 44px; top: 62px;
  }
  .brand-name {
    font-weight: 800; font-size: 52px; line-height: 1;
    color: var(--ink); letter-spacing: 1px;
  }
  .brand-tagline {
    margin-top: 8px;
    font-weight: 300; font-size: 16px; letter-spacing: 4.5px;
    color: var(--tagline);
  }
  .footer-wave {
    position: absolute; left: 0; top: 0;
    width: 618px; height: 800px;
  }
  .contact {
    position: absolute; right: 26px; top: 614px;
    list-style: none; text-align: right;
    color: var(--text-light);
    font-size: 11.5px; line-height: 17px; font-weight: 400;
  }
  .contact li { display: flex; justify-content: flex-end; align-items: center; gap: 6px; }
  .contact svg { width: 11px; height: 11px; flex: none; }
  .contact .plain { padding-right: 17px; }
  .contact .attorney { font-weight: 600; }
</style>
</head>
<body>
  <main class="letterhead">
    <svg class="footer-wave" viewBox="0 0 618 800" aria-hidden="true">
      <defs>
        <linearGradient id="stripe-fill" x1="0" y1="1" x2="1" y2="0">
          <stop offset="0" stop-color="var(--brand-deep)"/>
          <stop offset="1" stop-color="var(--brand-blue)"/>
        </linearGradient>
      </defs>
      <path class="stripe" fill="url(#stripe-fill)"
        d="M0,724 C215,722 330,684 395,604 C450,536 500,526 618,530 L618,538 C510,542 465,552 405,622 C335,705 210,748 0,748 Z"/>
      <path class="band" fill="var(--ink)"
        d="M0,748 C210,748 335,705 405,622 C465,552 510,542 618,538 L618,800 L0,800 Z"/>
      <path class="gap" fill="none" stroke="var(--paper)" stroke-width="2.5"
        d="M0,748 C210,748 335,705 405,622 C465,552 510,542 618,538"/>
    </svg>

    <header class="brand">
      <div class="brand-name">Bry7Legal</div>
      <div class="brand-tagline">MOVE WITH PURPOSE</div>
    </header>

    <ul class="contact">
      <li class="plain attorney">Anselmo R Quintara III</li>
      <li class="plain">2847 Larkspur Blvd, Ste</li>
      <li class="plain">300, Dallas, TX 75204</li>
      <li>877-482-6017
        <svg viewBox="0 0 12 12" aria-label="Phone"><path fill="var(--brand-blue)" d="M2.5 1 L4.5 1 L5 3.5 L3.8 4.4 C4.5 6 6 7.5 7.6 8.2 L8.5 7 L11 7.5 L11 9.5 C11 10.4 10.3 11 9.5 11 C5 10.6 1.4 7 1 2.5 C1 1.7 1.6 1 2.5 1 Z"/></svg>
      </li>
      <li>469-738-1452
        <svg viewBox="0 0 12 12" aria-label="Fax"><g fill="var(--brand-blue)"><rect x="3" y="1" width="6" height="3"/><rect x="1" y="4.5" width="10" height="4.5" rx="1"/><rect x="3" y="8" width="6" height="3"/></g></svg>
      </li>
      <li>bry@bry7legal.example
        <svg viewBox="0 0 12 12" aria-label="Email"><rect x="1" y="2.5" width="10" height="7" fill="var(--brand-blue)"/><path d="M1 2.5 L6 6.5 L11 2.5" fill="none" stroke="var(--ink)" stroke-width="1"/></svg>
      </li>
      <li>www.bry7legal.example
        <svg viewBox="0 0 12 12" aria-label="Website"><circle cx="6" cy="6" r="5" fill="var(--brand-blue)"/><path d="M1 6 H11 M6 1 C3.5 3.5 3.5 8.5 6 11 M6 1 C8.5 3.5 8.5 8.5 6 11" fill="none" stroke="var(--ink)" stroke-width="0.8"/></svg>
      </li>
    </ul>
  </main>
</body>
</html>
```